RM Installations Web Site Design

Need a basic site to show clients a little about what we do. We are a custom audio video company in the high-end residential market. Need a few basic but professional pages to show past projects and products we sell. No e-commerce. Should include my new logo from MarkBazaar.

Industry/Entity Type

Residential

Number of Pages Required

2 page

Font styles to use
Serif
Sans Serif

Colors
f78f20

Requirements
Must have
• Company Logo, Send feedback page
Nice to have
• I have no ideas about design, but I do know what I like and dislike when I see it.

```html
<!DOCTYPE html>
<html lang="en">
<head>
<meta charset="utf-8">
<title>RM Installations – Audio Video Control</title>
<link href="https://fonts.googleapis.com/css2?family=Oswald:wght@400;500&family=Lato:wght@400;700&display=swap" rel="stylesheet">
<style>
:root{
  --orange:#f78f20;
  --orange-dark:#e07810;
  --ink:#1d1d1d;
  --nav:#1f1f1f;
  --text:#555;
  --muted:#777;
  --about-bg:#e9ebe8;
  --team-bg:#f2f2f2;
  --footer:#1f1f1f;
  --footer-base:#151515;
  --footer-heading:#c4c4c4;
  --white:#fff;
}
*{margin:0;padding:0;box-sizing:border-box}
html,body{width:1200px;height:2236px;overflow:hidden}
body{position:relative;font-family:'Lato',sans-serif;color:var(--text);background:var(--white)}
.abs{position:absolute}
.heading{font-family:'Oswald',sans-serif;font-weight:500;text-transform:uppercase;font-size:33px;color:var(--ink);letter-spacing:.3px}
.heading span{color:var(--orange)}
.heading.on-dark{color:var(--footer-heading)}
.center{left:0;width:1200px;text-align:center}

/* header */
.site-header{top:0;left:0;width:1200px;height:100px;background:linear-gradient(90deg,#f59a2a,#f7a840 50%,#f39320)}
.brand{left:131px;top:28px;display:flex;align-items:center;gap:12px}
.brand-mark{width:36px;height:36px;background:var(--ink)}
.brand-name{font-family:'Lato',sans-serif;font-weight:700;font-size:22px;color:var(--ink);line-height:1}
.header-contact{top:28px;display:flex;align-items:center;gap:16px}
.header-contact small{display:block;font-size:13px;color:var(--white)}
.header-contact b{display:block;font-weight:400;font-size:18px;color:var(--white)}
.diamond{width:42px;height:42px;display:flex;align-items:center;justify-content:center}
.diamond::before{content:"";position:absolute;width:30px;height:30px;background:var(--ink);transform:rotate(45deg);border-radius:5px}
.diamond svg{position:relative;width:16px;height:16px}

/* nav */
.main-nav{top:100px;left:0;width:1200px;height:49px;background:var(--nav);display:flex;align-items:center;padding-left:131px;font-size:15px;color:#ccc}
.main-nav a{color:#ccc;text-decoration:none;padding:0 24px;line-height:49px;position:relative}
.main-nav a+a::before{content:"|";position:absolute;left:-3px;color:#777}
.main-nav a.active{background:var(--orange);color:var(--white);padding:0 24px}
.main-nav a.active+a::before{content:none}

/* hero */
.hero{top:149px;left:0;width:1200px;height:450px;background:linear-gradient(180deg,#e9e6e1 0%,#cfc9c1 55%,#9a928a 100%)}
.hero-caption{top:507px;left:0;width:1200px;height:92px;background:rgba(20,20,20,.8);display:flex;align-items:center}
.hero-title{width:447px;height:92px;background:rgba(0,0,0,.55);padding:10px 0 0 133px;font-family:'Oswald',sans-serif;font-weight:500;font-size:27px;line-height:34px;color:var(--white)}
.hero-title span{color:var(--orange)}
.hero-text{padding-left:32px;font-size:19px;line-height:27px;color:#eee}
.slide-arrow{width:36px;height:36px;background:#2a2a2a;display:flex;align-items:center;justify-content:center}
.slide-arrow.light{background:#c9c9c9}

/* services */
.card{width:216px;height:280px;background:var(--orange);top:702px}
.card .photo{height:158px}
.card h3{font-family:'Oswald',sans-serif;font-weight:400;font-size:17px;color:var(--white);padding:10px 11px 6px}
.card p{font-size:13px;line-height:19px;color:#fde7cc;padding:0 11px}
.card a{display:block;font-size:11px;color:var(--ink);padding:8px 11px 0;text-decoration:none}

/* about & team */
.about{top:1020px;left:0;width:613px;height:366px;background:var(--about-bg)}
.team{top:1020px;left:613px;width:587px;height:366px;background:var(--team-bg)}
.about-title{left:131px;top:1055px;display:flex;align-items:center;gap:14px}
.about-title .sub{font-family:'Lato',sans-serif;font-weight:700;font-size:16px;color:var(--ink);border-left:2px solid var(--ink);padding-left:8px;text-transform:none}
.about-text{left:131px;top:1118px;width:446px;font-size:12.5px;line-height:19.5px;color:var(--text)}
.about-text p+p{margin-top:20px}
.btn-read{left:131px;top:1311px;width:94px;height:32px;background:var(--orange);border-bottom:3px solid #b8600c;border-radius:3px;font-size:11px;color:var(--ink);text-align:center;line-height:30px}
.member{left:656px;display:flex;gap:22px}
.member .portrait{width:88px;height:88px;display:flex;align-items:center;justify-content:center;flex:none}
.member .portrait i{width:62px;height:62px;transform:rotate(45deg);border-radius:10px;background:linear-gradient(135deg,#d8d8d8,#9c9c9c)}
.member h4{font-family:'Oswald',sans-serif;font-weight:400;font-size:17px;color:var(--orange)}
.member em{display:block;font-size:12px;color:var(--muted);margin:2px 0 8px}
.member p{width:290px;font-size:12.5px;line-height:19px}

/* past projects */
.project{top:1489px;width:216px}
.project .photo{height:158px}
.project h3{font-family:'Oswald',sans-serif;font-weight:400;font-size:17px;color:var(--orange);margin-top:14px}

/* contact */
.contact{top:1705px;left:0;width:1200px;height:483px;background:var(--footer)}
.col-title{font-family:'Oswald',sans-serif;font-weight:400;font-size:17px;color:var(--white)}
.field{left:131px;width:382px;height:42px;background:var(--white);border-radius:3px;font-size:15px;color:#888;padding:11px 13px}
.btn-submit{left:131px;top:2123px;width:119px;height:42px;background:var(--orange);font-family:'Lato',sans-serif;font-weight:700;font-size:19px;color:var(--white);text-align:center;line-height:42px;text-transform:uppercase}
.detail{left:559px;display:flex;align-items:center;gap:10px;color:#ddd;font-size:15px}
.detail .diamond{flex:none}
.detail .diamond::before{background:var(--orange)}
.detail p{font-size:12.5px;line-height:19px;width:250px}
.social{left:917px;display:flex;align-items:center;gap:16px;font-size:12px;color:#ccc;letter-spacing:.3px}
.social .diamond::before{background:var(--c)}
.site-footer{top:2188px;left:0;width:1200px;height:48px;background:var(--footer-base);text-align:center;line-height:48px;font-size:12px;color:#bbb}
</style>
</head>
<body>

<header class="site-header abs">
  <div class="brand abs"><div class="brand-mark"></div><div class="brand-name">RM Installations</div></div>
  <div class="header-contact abs" style="left:662px">
    <div class="diamond"><svg viewBox="0 0 16 16"><path fill="#f78f20" d="M3 1l3 3-2 2c1 2 3 4 5 5l2-2 3 3-2 3C7 15 1 9 1 3z"/></svg></div>
    <div><small>Call Us</small><b>(555)-010-2040</b></div>
  </div>
  <div class="header-contact abs" style="left:885px">
    <div class="diamond"><svg viewBox="0 0 16 16"><path fill="#f78f20" d="M1 4h14v9H1z"/><path d="M1 4l7 5 7-5" stroke="#1d1d1d" stroke-width="1.4" fill="none"/></svg></div>
    <div><small>Email Us</small><b>info@rminstall.com</b></div>
  </div>
</header>

<nav class="main-nav abs">
  <a class="active">HOME</a><a>OUR TEAM</a><a>PRODUCTS</a><a>OUR SERVICES</a><a>PAST PROJECT</a><a>FEEDBACK</a><a>CONTACT US</a>
</nav>

<section class="hero abs" role="img" aria-label="Living room home theater with large TV flanked by tower speakers"></section>
<div class="slide-arrow abs" style="left:7px;top:344px"><svg width="12" height="14"><path d="M9 1L3 7l6 6" stroke="#fff" stroke-width="2.5" fill="none"/></svg></div>
<div class="slide-arrow abs" style="left:1157px;top:344px"><svg width="12" height="14"><path d="M3 1l6 6-6 6" stroke="#fff" stroke-width="2.5" fill="none"/></svg></div>
<div class="hero-caption abs">
  <div class="hero-title">Welcom to<br><span>RM Installations</span></div>
  <div class="hero-text">We expert in Residential Cinemas Make your Home Safe &amp; Secure With<br>our largest audio video control system</div>
</div>

<h2 class="heading abs center" style="top:636px"><span>Our</span> Services</h2>
<div class="slide-arrow light abs" style="left:94px;top:824px"><svg width="12" height="14"><path d="M9 1L3 7l6 6" stroke="#fff" stroke-width="2.5" fill="none"/></svg></div>
<div class="slide-arrow light abs" style="left:1069px;top:824px"><svg width="12" height="14"><path d="M3 1l6 6-6 6" stroke="#fff" stroke-width="2.5" fill="none"/></svg></div>
<article class="card abs" style="left:131px"><div class="photo" role="img" aria-label="Dark red home cinema room with recliners" style="background:linear-gradient(160deg,#7a2a2a,#2a1414)"></div><h3>Residential Cinemas</h3><p>Lor ipsumdolorsitac nsectetur adipiscing elit &nbsp;d.uis.</p><a>View Details ››</a></article>
<article class="card abs" style="left:371px"><div class="photo" role="img" aria-label="Consultant showing a design on a laptop to a client" style="background:linear-gradient(160deg,#e6d2bc,#8a7562)"></div><h3>Design And Consultations</h3><p>Lor ipsumdolorsitac nsectetur adipiscing elit &nbsp;d.uis.</p><a>View Details ››</a></article>
<article class="card abs" style="left:613px"><div class="photo" role="img" aria-label="Hand holding a lighting remote over a sofa" style="background:linear-gradient(160deg,#9a7660,#3d2a22)"></div><h3>Automated Lighting Control</h3><p>Lor ipsumdolorsitac nsectetur adipiscing elit &nbsp;d.uis.</p><a>View Details ››</a></article>
<article class="card abs" style="left:853px"><div class="photo" role="img" aria-label="Outdoor TV mounted on a stone wall" style="background:linear-gradient(160deg,#9d8a76,#4c4036)"></div><h3>Outdoor Audio and Video</h3><p>Lor ipsumdolorsitac nsectetur adipiscing elit &nbsp;d.uis.</p><a>View Details ››</a></article>

<section class="about abs"></section>
<section class="team abs"></section>
<div class="about-title abs"><h2 class="heading"><span>About</span></h2><div class="heading sub">RM Installations</div></div>
<div class="about-text abs">
  <p>Lorem ipsum dolor sit amet, consectetuer adipiscing elit, sed diam nonummy nibh euismod tincidunt ut laoreet dolore magna aliquam erat volutpat. Ut wisi enim ad minim veniam, quis nostrud exerci tation ullamcorper suscipit lobortis nisl ut aliquip ex ea commodo consequat.</p>
  <p>Duis autem vel eum iriure dolor in hendrerit in vulputate velit esse molestie consequat, vel illum dolore eu feugiat nulla facilisis at vero eros et accumsan et iusto odio dignissim qui blandit praesent luptatum zzril delenit augue duis dolore te feugait nulla facilisi.</p>
</div>
<div class="btn-read abs">Read More ››</div>
<h2 class="heading abs" style="left:656px;top:1055px"><span>Our</span> Team</h2>
<div class="member abs" style="top:1125px"><div class="portrait" role="img" aria-label="Portrait of team director"><i></i></div><div><h4>Dan Mercer</h4><em>Director</em><p>Ut wisi enim ad minim veniam, quis nostrud exerci tation ullamcorper suscipit lobortis nisl ut aliquip.</p></div></div>
<div class="member abs" style="top:1247px"><div class="portrait" role="img" aria-label="Portrait of team director"><i></i></div><div><h4>Lena Ford</h4><em>Director</em><p>Ut wisi enim ad minim veniam, quis nostrud exerci tation ullamcorper suscipit lobortis nisl ut aliquip.</p></div></div>

<h2 class="heading abs center" style="top:1425px"><span>Past</span> Project</h2>
<div class="slide-arrow light abs" style="left:94px;top:1550px"><svg width="12" height="14"><path d="M9 1L3 7l6 6" stroke="#fff" stroke-width="2.5" fill="none"/></svg></div>
<div class="slide-arrow light abs" style="left:1069px;top:1550px"><svg width="12" height="14"><path d="M3 1l6 6-6 6" stroke="#fff" stroke-width="2.5" fill="none"/></svg></div>
<article class="project abs" style="left:131px"><div class="photo" role="img" aria-label="Finished home cinema lounge" style="background:linear-gradient(160deg,#6b4a32,#2a1c14)"></div><h3>Residential Cinemas</h3></article>
<article class="project abs" style="left:371px"><div class="photo" role="img" aria-label="Multi-screen control desk installation" style="background:linear-gradient(160deg,#8d8a86,#2e2c2a)"></div><h3>Design And Consultations</h3></article>
<article class="project abs" style="left:613px"><div class="photo" role="img" aria-label="Orange room with TV, speakers and red chairs" style="background:linear-gradient(160deg,#f29a3a,#c24a20)"></div><h3>Automated Lighting Control</h3></article>
<article class="project abs" style="left:853px"><div class="photo" role="img" aria-label="Living room with wall TV and tablet control" style="background:linear-gradient(160deg,#d8d4cf,#6a5e52)"></div><h3>Outdoor Audio and Video</h3></article>

<section class="contact abs"></section>
<h2 class="heading on-dark abs center" style="top:1742px"><span>Contact</span> Us</h2>
<h3 class="col-title abs" style="left:131px;top:1814px">FeedBack</h3>
<div class="field abs" style="top:1860px">Name</div>
<div class="field abs" style="top:1917px">Email</div>
<div class="field abs" style="top:1974px">Phone</div>
<div class="field abs" style="top:2030px;height:78px">Message</div>
<div class="btn-submit abs">Submit</div>

<h3 class="col-title abs" style="left:559px;top:1814px">Contact Detail</h3>
<div class="detail abs" style="top:1857px"><div class="diamond"><svg viewBox="0 0 16 16"><path fill="#fff" d="M8 1a5 5 0 015 5c0 4-5 9-5 9S3 10 3 6a5 5 0 015-5z"/><circle cx="8" cy="6" r="2" fill="#f78f20"/></svg></div><p>Lorem ipsum dolor sit amet, consectetuer adipiscing elit, sed diam nonummy nibh euismod.</p></div>
<div class="detail abs" style="top:1942px"><div class="diamond"><svg viewBox="0 0 16 16"><path fill="#fff" d="M3 1l3 3-2 2c1 2 3 4 5 5l2-2 3 3-2 3C7 15 1 9 1 3z"/></svg></div>(555)-010-2040</div>
<div class="detail abs" style="top:2003px"><div class="diamond"><svg viewBox="0 0 16 16"><rect x="2" y="4" width="12" height="10" fill="#fff"/><rect x="5" y="1" width="6" height="4" fill="#fff"/><rect x="5" y="7" width="6" height="2" fill="#f78f20"/></svg></div>(555)-010-2040</div>
<div class="detail abs" style="top:2066px"><div class="diamond"><svg viewBox="0 0 16 16"><path fill="#fff" d="M1 4h14v9H1z"/><path d="M1 4l7 5 7-5" stroke="#f78f20" stroke-width="1.4" fill="none"/></svg></div>info@rminstall.com</div>

<h3 class="col-title abs" style="left:917px;top:1814px">Follow Us</h3>
<div class="social abs" style="top:1859px;--c:#2a5fa8"><div class="diamond"></div>SOCIALBOOK</div>
<div class="social abs" style="top:1918px;--c:#2bb3d6"><div class="diamond"></div>CHIRPER</div>
<div class="social abs" style="top:1977px;--c:#1f7fb5"><div class="diamond"></div>WORKNET</div>
<div class="social abs" style="top:2037px;--c:#d9503c"><div class="diamond"></div>CIRCLEPLUS</div>

<footer class="site-footer abs">© 2015 RM Installations. All rights reserved.</footer>

</body>
</html>
```